HearthMile business card and stationary design

We are looking for a simple yet elegant design for our mortgage company business card and stationary.

The card should include:
Name (Marcus Pell)
Title (CEO)
Phone Number (732-555-0182)
Address (48 Birchwell Court, Suite 314, Hazlet, NJ 07730)
Email (email@hearthmile.example)
"NMLS" i.e. (NMLS 61947)
"Company NMLS" (Company NMLS 274615)

Contact Information for Business Card

See above

```html
<!DOCTYPE html>
<html lang="en">
<head>
<meta charset="utf-8">
<title>HearthMile Business Card</title>
<link href="https://fonts.googleapis.com/css2?family=Roboto:wght@400;500;700&display=swap" rel="stylesheet">
<style>
  :root {
    --page-bg: #d9d9d9;
    --card-white: #ffffff;
    --navy: #1b2733;
    --navy-light: #2f4559;
    --sky: #1ba9e6;
    --ink: #2d2d2d;
    --white: #ffffff;
  }
  * { margin: 0; padding: 0; box-sizing: border-box; }
  html, body {
    width: 1200px; height: 1200px; overflow: hidden;
    background: var(--page-bg);
    font-family: "Roboto", Arial, sans-serif;
  }
  .card {
    position: absolute; left: 200px;
    width: 800px; height: 457px; overflow: hidden;
  }
  .card-front { top: 80px; background: var(--card-white); }
  .card-back { top: 663px; background: var(--navy); }

  .name-band {
    position: absolute; left: 0; top: 68px;
    width: 459px; height: 64px; background: var(--navy);
  }
  .holder-name {
    position: absolute; left: 55px; top: 4px;
    font-size: 27px; font-weight: 700; color: var(--sky);
  }
  .holder-title {
    position: absolute; left: 55px; top: 36px;
    font-size: 18px; font-weight: 500; color: var(--white);
  }
  .brand-front {
    position: absolute; right: 50px; top: 80px;
    font-size: 56px; font-weight: 400; color: var(--sky);
    letter-spacing: 0.5px; line-height: 1;
  }

  .contact-list {
    position: absolute; left: 56px; top: 323px;
    list-style: none; font-size: 18px; color: var(--ink);
    line-height: 22.5px;
  }
  .contact-list li { display: flex; align-items: center; gap: 8px; }
  .contact-list svg { width: 15px; height: 15px; flex: none; }
  .contact-list .company-nmls { margin-top: 3px; }

  .office {
    position: absolute; right: 48px; top: 318px;
    text-align: right; font-size: 18px; color: var(--ink);
    line-height: 22.5px; font-style: normal;
  }
  .office .nmls { margin-top: 7px; display: block; }

  .back-decoration {
    position: absolute; inset: 0;
    background: linear-gradient(160deg, rgba(47,69,89,0.3) 0%, rgba(27,39,51,0) 60%);
  }
  .brand-back {
    position: absolute; right: 88px; top: 322px; text-align: right;
  }
  .brand-back .wordmark {
    font-size: 60px; font-weight: 400; color: var(--white); line-height: 1;
  }
  .brand-back .web {
    margin-top: 6px; font-size: 16px; font-weight: 500;
    letter-spacing: 6px; color: var(--white); margin-right: -6px;
  }
</style>
</head>
<body>
  <section class="card card-front">
    <div class="name-band">
      <div class="holder-name">Marcus Pell</div>
      <div class="holder-title">CEO</div>
    </div>
    <div class="brand-front">HearthMile</div>

    <ul class="contact-list">
      <li>
        <svg viewBox="0 0 16 16"><path fill="#1ba9e6" d="M3.6 1.2l2.4 2.6-1.3 2a8.5 8.5 0 0 0 5.5 5.5l2-1.3 2.6 2.4-1.6 2.3C6.9 14.6 1.4 9.1 1.3 2.8z"/></svg>
        732-555-0182
      </li>
      <li>
        <svg viewBox="0 0 16 16"><rect x="1" y="3.5" width="14" height="9.5" fill="#1ba9e6"/><path d="M1.5 4l6.5 5 6.5-5" stroke="#fff" stroke-width="1.3" fill="none"/></svg>
        info@hearthmile.example
      </li>
      <li>
        <svg viewBox="0 0 16 16"><circle cx="8" cy="8" r="7" fill="#1ba9e6"/><path d="M5 4.5c1.5 0 2 1.2 1.3 2.2-.8 1 .2 2 1.2 2.5s.3 2.5-.5 3.3M10 3c-.5 1.2.5 2 1.5 1.8" stroke="#fff" stroke-width="1.2" fill="none"/></svg>
        hearthmile.example
      </li>
      <li class="company-nmls">Company NMLS 274615</li>
    </ul>

    <address class="office">
      48 Birchwell Court<br>
      Suite 314<br>
      Larkfield, NJ 07099
      <span class="nmls">NMLS I.E. 61947</span>
    </address>
  </section>

  <section class="card card-back">
    <div class="back-decoration" role="img" aria-label="Large faint brand symbol decoration in muted slate blue"></div>
    <div class="brand-back">
      <div class="wordmark">HearthMile</div>
      <div class="web">www.HearthMile.example</div>
    </div>
  </section>
</body>
</html>
```